Fun relaxed Travel Photography Business Card*

Require a fun, funky and quirky but rememberable business card for a travel photographer

Industry/Entity Type

Photographer

Contact Information for Business Card

Front Card

(my name) Lenn D.

Travel Photographer ( small under travel photographer) “self-proclaimed”

(website logo) wanderingsoflenn.net

(Instagram logo) @wanderings_of_lenn

(Instagram logo) @wanderings_of_lenn_2.0 (backup for when Instagram puts Lenn on timeout for bad behaviour)

Tel: N/A (removing the potential awkwardness of me not replying)

Email: (see above)

Back Card

Offending people since 1986

(Bottom right corner) “p.s. travelling made me fatTER”

Font styles to use
Serif

Colors

Designer to choose colors to be used in the design.

Requirements
Must have
• a camera
• a similar cartoon version of me as the "logo" see attached files, try to make as similar as possible

```html
<!DOCTYPE html>
<html lang="en">
<head>
<meta charset="utf-8">
<title>Lenn D. — Travel Photographer Business Card</title>
<link rel="stylesheet" href="https://fonts.googleapis.com/css2?family=Lato:wght@300;400;700&family=Josefin+Sans:wght@300;400;600&display=swap">
<style>
  :root {
    --ink: #111111;
    --paper: #ffffff;
    --backdrop: #d9d9d9;
    --night: #0b0b0b;
    --night-soft: #1c1c1c;
    --muted: #cfcfcf;
  }
  * { box-sizing: border-box; margin: 0; padding: 0; }
  html, body {
    width: 1200px; height: 1015px; overflow: hidden;
    background: var(--backdrop);
  }
  .stage {
    width: 1200px; height: 1015px;
    display: flex; flex-direction: column; align-items: center; justify-content: center;
    gap: 44px;
  }
  .card {
    width: 740px; height: 420px;
    position: relative; overflow: hidden;
    box-shadow: 0 14px 30px rgba(0,0,0,0.25);
  }

  /* Back */
  .card--back { background: var(--night); color: var(--paper); }
  .back-pattern {
    position: absolute; inset: 0;
    background: radial-gradient(ellipse at center, var(--night-soft) 0%, var(--night) 75%);
  }
  .back-mark {
    position: absolute; left: 50%; top: 150px; transform: translateX(-50%);
    display: flex; align-items: center; gap: 10px;
    font-family: "Lato", sans-serif; font-weight: 400; font-size: 22px; color: var(--paper);
  }
  .back-mark__square { width: 18px; height: 18px; border: 2px solid var(--paper); }
  .tagline {
    position: absolute; bottom: 34px;
    font-family: "Lato", sans-serif; font-weight: 400; font-size: 17px; color: var(--muted);
    letter-spacing: 0.2px;
  }
  .tagline--left { left: 36px; }
  .tagline--right { right: 36px; }

  /* Front */
  .card--front { background: var(--paper); color: var(--ink); }
  .identity {
    position: absolute; top: 52px; left: 50%; transform: translateX(-50%);
    display: flex; align-items: center; gap: 18px;
  }
  .identity__square { width: 58px; height: 58px; border: 3px solid var(--ink); border-radius: 6px; }
  .identity__text { border-left: 3px solid var(--ink); padding-left: 12px; }
  .identity__name {
    font-family: "Josefin Sans", sans-serif; font-weight: 300; font-size: 56px; line-height: 1;
  }
  .identity__role {
    font-family: "Josefin Sans", sans-serif; font-weight: 600; font-size: 15px; letter-spacing: 1.5px;
    border-top: 2px solid var(--ink); margin-top: 4px; padding-top: 3px;
  }
  .identity__note {
    font-family: "Josefin Sans", sans-serif; font-weight: 600; font-size: 9px; letter-spacing: 1.2px;
    text-align: right;
  }
  .contacts {
    position: absolute; top: 200px; left: 0; right: 0;
    display: flex; justify-content: center; align-items: stretch; gap: 26px;
    font-family: "Josefin Sans", sans-serif; font-weight: 400; font-size: 19px;
  }
  .contacts__col { display: flex; flex-direction: column; gap: 10px; justify-content: center; }
  .contacts__col--social { align-items: flex-end; }
  .contacts__divider { width: 2px; background: var(--ink); }
  .contact { display: flex; align-items: center; gap: 10px; }
  .contact__square { width: 16px; height: 16px; border: 2px solid var(--ink); border-radius: 3px; }
  .contact svg { width: 18px; height: 18px; }
  .web-band {
    position: absolute; left: 0; right: 0; bottom: 0; height: 64px;
    background: var(--night); color: var(--paper);
    display: flex; align-items: center; justify-content: center;
    font-family: "Josefin Sans", sans-serif; font-weight: 600; font-size: 24px; letter-spacing: 2px;
  }
</style>
</head>
<body>
<main class="stage">
  <section class="card card--back">
    <div class="back-pattern" role="img" aria-label="Faint repeating pattern of the camera logo mark"></div>
    <div class="back-mark"><span class="back-mark__square"></span>Lenn D.</div>
    <p class="tagline tagline--left">Offending people since 1986</p>
    <p class="tagline tagline--right">p.s. travelling made me fatter</p>
  </section>

  <section class="card card--front">
    <div class="identity">
      <span class="identity__square"></span>
      <div class="identity__text">
        <div class="identity__name">Lenn D.</div>
        <div class="identity__role">TRAVEL PHOTOGRAPHER</div>
        <div class="identity__note">SELF-PROCLAIMED</div>
      </div>
    </div>

    <div class="contacts">
      <div class="contacts__col contacts__col--social">
        <div class="contact">@wanderings_of_lenn <span class="contact__square"></span></div>
        <div class="contact">@wanderings_of_lenn_2.0 <span class="contact__square"></span></div>
      </div>
      <div class="contacts__divider"></div>
      <div class="contacts__col">
        <div class="contact">
          <svg viewBox="0 0 24 24" aria-hidden="true"><path fill="currentColor" d="M6.6 10.8a15 15 0 0 0 6.6 6.6l2.2-2.2a1 1 0 0 1 1-.25 11.4 11.4 0 0 0 3.6.57 1 1 0 0 1 1 1V20a1 1 0 0 1-1 1A17 17 0 0 1 3 4a1 1 0 0 1 1-1h3.5a1 1 0 0 1 1 1c0 1.25.2 2.45.57 3.6a1 1 0 0 1-.25 1z"/></svg>
          555 0142 7788
        </div>
        <div class="contact">
          <svg viewBox="0 0 24 24" aria-hidden="true"><path fill="currentColor" d="M2 5h20v14H2zm2 2v.5l8 5 8-5V7l-8 5z"/></svg>
          info@wanderingsoflenn.net
        </div>
        <div class="contact">wanderingsoflenn.net</div>
      </div>
    </div>

    <div class="web-band">www.wanderingsoflenn.net</div>
  </section>
</main>
</body>
</html>
```